Business Card Design For A Renovation Contractor Company

We need a business card for a new company based in Singapore, our company name is "RB Tolvane". We are a renovation contractor that builds designs into reality. We build more of F&B restaurants, retail stores and commercial offices. We work very closely with designers. The final design should communicate to our client that we are a company that you can trust, that will plan and complete your project without giving you a headache. I like my client to remember my company as "RB". The beauty of SIMPLE is important.

Industry/Entity Type

Contractor

Requirements
Nice to have
• Black or Red base

```html
<!DOCTYPE html>
<html lang="en">
<head>
<meta charset="utf-8">
<title>RB Tolvane — Business Card</title>
<link rel="stylesheet" href="https://fonts.googleapis.com/css2?family=Jost:wght@400;500;700&display=swap">
<style>
  :root {
    --brand-red: #e52328;
    --ink: #1a1a1a;
    --muted: #555555;
    --rule: #9a9a9a;
    --card: #ffffff;
    --backdrop: #e4e4ea;
  }
  * { box-sizing: border-box; margin: 0; padding: 0; }
  html, body {
    width: 1200px; height: 987px; overflow: hidden;
    background: var(--backdrop);
    font-family: "Jost", "Futura", sans-serif;
    color: var(--ink);
  }
  .sheet {
    position: relative; width: 1200px; height: 987px;
    display: flex; flex-direction: column; align-items: center; justify-content: center; gap: 64px;
  }
  .card {
    position: relative; width: 640px; height: 366px;
    background: var(--card); border-radius: 22px;
    box-shadow: 0 6px 18px rgba(0,0,0,0.12);
    overflow: hidden;
  }

  /* Back side */
  .card-back { display: flex; flex-direction: column; align-items: center; justify-content: center; }
  .back-mark { display: flex; align-items: center; gap: 22px; }
  .back-mark .dot {
    width: 120px; height: 120px; border-radius: 50%;
    background: var(--ink); border: 3px solid var(--brand-red);
  }
  .back-mark .name { font-size: 52px; font-weight: 500; color: var(--ink); letter-spacing: 1px; }
  .back-url {
    margin-top: 40px; font-size: 22px; letter-spacing: 5px; color: var(--ink);
  }
  .back-url .accent { color: var(--brand-red); }

  /* Front side */
  .identity {
    position: absolute; left: 44px; top: 62px; width: 300px;
  }
  .identity .mark-row { display: flex; align-items: center; gap: 12px; }
  .identity .dot {
    width: 46px; height: 46px; border-radius: 50%;
    background: var(--ink); border: 2px solid var(--brand-red);
  }
  .identity .name { font-size: 44px; font-weight: 500; color: var(--ink); line-height: 1; }
  .identity .tagline {
    margin-top: 8px; padding-top: 4px; border-top: 1px solid var(--ink);
    font-size: 17px; color: var(--ink);
  }
  .divider {
    position: absolute; left: 366px; top: 40px; width: 1px; height: 190px;
    background: linear-gradient(to bottom, transparent, var(--rule), transparent);
  }
  .contact { position: absolute; left: 388px; top: 44px; }
  .contact .person { font-size: 28px; font-weight: 700; color: var(--brand-red); line-height: 1.05; }
  .contact .role { font-size: 18px; color: var(--muted); margin-bottom: 12px; }
  .contact ul { list-style: none; }
  .contact li { display: flex; align-items: center; gap: 8px; font-size: 19px; color: var(--ink); line-height: 1.45; }
  .contact svg { width: 13px; height: 13px; fill: var(--brand-red); flex: none; }
  .address-band {
    position: absolute; left: 0; right: 0; top: 262px; height: 40px;
    background: var(--brand-red);
    display: flex; align-items: center; padding-left: 44px;
    font-size: 19px; color: #ffffff; letter-spacing: 0.6px;
  }
  .band-rule { position: absolute; left: 0; right: 0; height: 1px; background: var(--rule); }
  .band-rule.top { top: 254px; }
  .band-rule.bottom { top: 310px; }
</style>
</head>
<body>
<main class="sheet">

  <section class="card card-back" aria-label="Card back">
    <div class="back-mark">
      <span class="dot" aria-hidden="true"></span>
      <span class="name">RB Tolvane</span>
    </div>
    <p class="back-url">www.<span class="accent">rbtolvane</span>.com</p>
  </section>

  <section class="card card-front" aria-label="Card front">
    <div class="identity">
      <div class="mark-row">
        <span class="dot" aria-hidden="true"></span>
        <span class="name">RB Tolvane</span>
      </div>
      <p class="tagline">turning every plan into space</p>
    </div>

    <div class="divider"></div>

    <div class="contact">
      <p class="person">Your Name</p>
      <p class="role">Title</p>
      <ul>
        <li><svg viewBox="0 0 16 16"><circle cx="8" cy="8" r="8"/><path d="M5 4h2l1 2-1 1c.5 1 1.5 2 2.5 2.5l1-1 2 1v2c-4 0-7.5-3.5-7.5-7.5z" fill="#fff"/></svg>123-456-7890</li>
        <li><svg viewBox="0 0 16 16"><rect x="4" y="0" width="8" height="16" rx="1.5"/><rect x="5.5" y="2" width="5" height="9" fill="#fff"/></svg>456-210-9873</li>
        <li><svg viewBox="0 0 16 16"><rect x="0" y="3" width="16" height="10" rx="1.5"/><path d="M1 4l7 5 7-5" stroke="#fff" stroke-width="1.4" fill="none"/></svg>info@rbtolvane.com</li>
        <li><svg viewBox="0 0 16 16"><circle cx="8" cy="8" r="8"/><path d="M1 8h14M8 1c3 3 3 11 0 14M8 1c-3 3-3 11 0 14" stroke="#fff" stroke-width="1.2" fill="none"/></svg>www.rbtolvane.com</li>
      </ul>
    </div>

    <div class="band-rule top"></div>
    <div class="address-band">Door No. Street Name City Name, State, Zip Code.</div>
    <div class="band-rule bottom"></div>
  </section>

</main>
</body>
</html>
```